Business Card Design for The Lending Nest Inc.

We need a business card design for our mortgage company: "The Lending Nest Inc."

Need to have Social Media Account on there as a possibility

```html
<!DOCTYPE html>
<html lang="en">
<head>
<meta charset="utf-8">
<title>The Lending Nest Inc. — Business Card</title>
<link rel="stylesheet" href="https://fonts.googleapis.com/css2?family=Lato:wght@400;700&display=swap">
<style>
  :root{
    --page:#ffffff;
    --card:#303030;
    --card-back:#323335;
    --panel:#111111;
    --stripe:#121212;
    --brand-blue:#1e5aa8;
    --muted-blue:#2f5080;
    --deep-blue:#28558f;
    --text-light:#ffffff;
    --text-grey:#c9c9c9;
    --icon:#2c4a78;
    --social-1:#4a8fd0;
    --social-2:#3d5f9e;
    --social-3:#3f7fc8;
  }
  html,body{margin:0;padding:0;overflow:hidden;background:var(--page);}
  .canvas{position:relative;width:1200px;height:1200px;background:var(--page);overflow:hidden;}
  .card{position:absolute;display:block;}
  .card--front{left:226px;top:145px;}
  .card--back{left:226px;top:623px;}
  .card text{font-family:'Lato',sans-serif;}
  .brand-name{fill:var(--brand-blue);font-weight:700;}
  .brand-sub{fill:var(--text-grey);font-weight:400;font-size:22px;}
  .contact{fill:var(--text-light);font-weight:400;}
</style>
</head>
<body>
<div class="canvas">

  <svg class="card card--front" width="719" height="410" viewBox="0 0 719 410" aria-label="Front of business card">
    <rect class="card-bg" width="719" height="410" fill="var(--card)"/>
    <polygon class="info-panel" points="0,29 321,29 351,313 0,313" fill="var(--panel)"/>
    <g class="diagonal-stripes" fill="var(--stripe)">
      <polygon points="534,0 576,0 482,410 432,410"/>
      <polygon points="598,0 638,0 544,410 496,410"/>
      <polygon points="662,0 702,0 608,410 558,410"/>
    </g>

    <g class="brand">
      <circle cx="61" cy="50" r="28" fill="none" stroke="var(--brand-blue)" stroke-width="3"/>
      <text class="brand-name" x="100" y="58" font-size="26">The Lending Nest</text>
      <text class="brand-sub" x="84" y="86">Lending Nest Inc</text>
    </g>

    <g class="contact-icons" fill="none" stroke="var(--icon)" stroke-width="3">
      <rect x="34" y="112" width="24" height="31" rx="3"/>
      <rect x="34" y="160" width="28" height="20"/>
      <polyline points="34,160 48,172 62,160"/>
      <rect x="34" y="197" width="28" height="18"/>
      <line x1="48" y1="215" x2="48" y2="222"/>
      <line x1="40" y1="222" x2="56" y2="222"/>
      <path d="M46,283 C38,270 33,264 33,256 A13,13 0 0 1 59,256 C59,264 54,270 46,283 Z" fill="var(--icon)" stroke="none"/>
      <circle cx="46" cy="256" r="5" fill="var(--panel)" stroke="none"/>
    </g>

    <g class="contact-details">
      <text class="contact" x="83" y="205" font-size="0"></text>
      <text class="contact" x="82" y="137" font-size="23">+555-201-880-4</text>
      <text class="contact" x="83" y="175" font-size="22">hello@lendingnest.example</text>
      <text class="contact" x="83" y="213" font-size="19">www.lendingnest.example</text>
      <text class="contact" x="83" y="251" font-size="17">Harbor Lane , Millbrook 4410</text>
      <text class="contact" x="83" y="271" font-size="17">North Terrace</text>
    </g>
  </svg>

  <svg class="card card--back" width="714" height="406" viewBox="0 0 714 406" aria-label="Back of business card">
    <rect class="card-bg" width="714" height="406" fill="var(--card-back)"/>
    <path class="accent-bar accent-bar--top" d="M333,0 H383 V110 A24,24 0 0 1 359,134 H357 A24,24 0 0 1 333,110 Z" fill="var(--muted-blue)"/>
    <path class="accent-bar accent-bar--bottom" d="M332,289 A24,24 0 0 1 356,265 H358 A24,24 0 0 1 382,289 V406 H332 Z" fill="var(--deep-blue)"/>

    <g class="brand">
      <circle cx="252" cy="190" r="31" fill="none" stroke="var(--brand-blue)" stroke-width="3"/>
      <text class="brand-name" x="296" y="200" font-size="30">The Lending Nest</text>
    </g>

    <g class="social-links">
      <circle cx="32" cy="286" r="21" fill="var(--social-1)"/>
      <circle cx="32" cy="335" r="21" fill="var(--social-2)"/>
      <circle cx="30" cy="384" r="22" fill="var(--social-3)"/>
    </g>
  </svg>

</div>
</body>
</html>
```